Design a poster that illustrates the six central pillars of our school district's efforts with students. The attached PDF outlines the six main competencies we aim for students to possess upon graduation. Each of the 6 has 3 bullet points for the poster as well. The title is "Profile of a Trailblazer". Our mascot is this attached winged wheel. The overall concept is that staff take kids when they are young and develop these 6 things when they graduate. Our colors are navy, red, and white. We will make this poster in a variety of sizes in offices, classrooms, and in digital spaces as well. On the PDF - ignore the column that says "Synthesis". That has nothing to do with this poster.

The district is Harlow Creek Public Schools https://www.harlowcreek-schools.example/

```html
<!DOCTYPE html>
<html lang="en">
<head>
<meta charset="utf-8">
<title>Profile of a Trailblazer — Harlow Creek Public Schools</title>
<link rel="stylesheet" href="https://fonts.googleapis.com/css2?family=Archivo+Black&family=Anton&family=Barlow+Condensed:wght@600;700&display=swap">
<style>
  :root {
    --navy: #0d0e3e;
    --red: #a01c22;
    --white: #ffffff;
    --card-text: #f4f4f8;
  }
  * { margin: 0; padding: 0; box-sizing: border-box; }
  html, body { width: 820px; height: 1200px; overflow: hidden; background: var(--white); }
  .poster {
    position: relative;
    width: 820px;
    height: 1200px;
    overflow: hidden;
    font-family: "Barlow Condensed", "Arial Narrow", sans-serif;
  }
  .poster__backdrop { position: absolute; inset: 0; width: 820px; height: 1200px; }

  .district-mark {
    position: absolute;
    left: 48px;
    top: 110px;
    width: 360px;
    display: flex;
    align-items: center;
    gap: 14px;
  }
  .district-mark__dot {
    width: 54px; height: 54px; border-radius: 50%;
    background: var(--navy);
    flex: none;
  }
  .district-mark__name {
    font-family: "Barlow Condensed", "Arial Narrow", sans-serif;
    font-weight: 700;
    font-size: 34px;
    line-height: 1.05;
    color: var(--navy);
  }

  .title {
    position: absolute;
    left: 440px;
    top: 44px;
    width: 290px;
    text-align: center;
  }
  .title__top {
    display: block;
    font-family: "Archivo Black", "Arial Black", sans-serif;
    font-size: 50px;
    line-height: 1;
    color: var(--red);
    letter-spacing: 1px;
  }
  .title__middle {
    display: flex;
    align-items: center;
    justify-content: center;
    gap: 10px;
    margin-top: 6px;
    font-family: "Archivo Black", "Arial Black", sans-serif;
    font-size: 32px;
    line-height: 1;
    color: var(--red);
  }
  .title__rule { display: block; width: 72px; height: 4px; background: var(--red); }
  .title__bottom {
    display: block;
    margin-top: 6px;
    font-family: "Anton", "Impact", sans-serif;
    font-size: 62px;
    line-height: 1;
    color: var(--navy);
    letter-spacing: 0.5px;
  }

  .pillar {
    position: absolute;
    background: var(--navy);
    border-radius: 9px;
    color: var(--card-text);
    padding: 16px 16px 14px 22px;
    overflow: hidden;
  }
  .pillar__name {
    font-weight: 700;
    font-size: 30px;
    line-height: 1.1;
    margin: 0 0 6px 6px;
  }
  .pillar__traits { list-style: none; }
  .pillar__trait {
    position: relative;
    padding-left: 14px;
    font-weight: 600;
    font-size: 19px;
    line-height: 22px;
    margin-bottom: 7px;
    letter-spacing: -0.3px;
  }
  .pillar__trait:last-child { margin-bottom: 0; }
  .pillar__trait::before {
    content: "";
    position: absolute;
    left: 0; top: 9px;
    width: 5px; height: 5px;
    border-radius: 50%;
    background: var(--card-text);
  }

  .pillar--communicator  { left: 66px;  top: 352px; width: 343px; height: 233px; }
  .pillar--critical      { left: 427px; top: 281px; width: 342px; height: 269px; }
  .pillar--responsible   { left: 66px;  top: 600px; width: 343px; height: 234px; }
  .pillar--adaptable     { left: 427px; top: 562px; width: 342px; height: 270px; }
  .pillar--collaborator  { left: 66px;  top: 852px; width: 343px; height: 266px; }
  .pillar--compassionate { left: 427px; top: 848px; width: 342px; height: 270px; }
</style>
</head>
<body>
<main class="poster">
  <svg class="poster__backdrop" viewBox="0 0 820 1200" aria-hidden="true">
    <rect width="820" height="1200" fill="var(--red)"/>
    <path d="M0 0 H820 V250 C700 222 560 242 420 288 C280 334 150 342 0 282 Z" fill="var(--navy)"/>
    <path d="M0 0 H820 V205 C700 182 560 210 420 258 C280 306 160 325 0 276 Z" fill="var(--white)"/>
  </svg>

  <div class="district-mark">
    <span class="district-mark__dot"></span>
    <span class="district-mark__name">Harlow Creek<br>Public Schools</span>
  </div>

  <h1 class="title">
    <span class="title__top">PROFILE</span>
    <span class="title__middle"><span class="title__rule"></span>OF A<span class="title__rule"></span></span>
    <span class="title__bottom">TRAILBLAZER</span>
  </h1>

  <section class="pillar pillar--critical">
    <h2 class="pillar__name">Critical Thinker</h2>
    <ul class="pillar__traits">
      <li class="pillar__trait">Questions, analyzes, and evaluates information from multiple sources.</li>
      <li class="pillar__trait">Identifies and solves complex problems creatively.</li>
      <li class="pillar__trait">Uses evidence and diverse perspectives to form reasoned conclusions and make informed</li>
    </ul>
  </section>

  <section class="pillar pillar--communicator">
    <h2 class="pillar__name">Communicator</h2>
    <ul class="pillar__traits">
      <li class="pillar__trait">Expresses ideas clearly and respectfully (written &amp; verbal).</li>
      <li class="pillar__trait">Listens actively and understands diverse perspectives.</li>
      <li class="pillar__trait">Adjusts communication to suit the audience and context.</li>
    </ul>
  </section>

  <section class="pillar pillar--adaptable">
    <h2 class="pillar__name">Adaptable</h2>
    <ul class="pillar__traits">
      <li class="pillar__trait">Responds productively to new situations, challenges, and feedback.</li>
      <li class="pillar__trait">Learns from new experiences and applies prior knowledge in evolving contexts.</li>
      <li class="pillar__trait">Adjusts behavior and approach to effectively engage with diverse groups and environments.</li>
    </ul>
  </section>

  <section class="pillar pillar--responsible">
    <h2 class="pillar__name">Responsible</h2>
    <ul class="pillar__traits">
      <li class="pillar__trait">Takes ownership of actions, choices, and commitments.</li>
      <li class="pillar__trait">Manages time, resources, and self to meet expectations.</li>
      <li class="pillar__trait">Acts with integrity and advocates for self and others.</li>
    </ul>
  </section>

  <section class="pillar pillar--collaborator">
    <h2 class="pillar__name">Collaborator</h2>
    <ul class="pillar__traits">
      <li class="pillar__trait">Contributes effectively and cooperatively to shared goals</li>
      <li class="pillar__trait">Listens actively and values diverse ideas and perspectives.</li>
      <li class="pillar__trait">Engages respectfully, compromising and leading when appropriate.</li>
    </ul>
  </section>

  <section class="pillar pillar--compassionate">
    <h2 class="pillar__name">Compassionate</h2>
    <ul class="pillar__traits">
      <li class="pillar__trait">Understands and acknowledges others' feelings, perspectives, and experiences.</li>
      <li class="pillar__trait">Responds with kindness, patience, and support.</li>
      <li class="pillar__trait">Seeks to connect with and contribute positively to the well-being of others</li>
    </ul>
  </section>
</main>
</body>
</html>
```